Modern business card design for professional copywriter

I'd like a business card design that I can use to have my cards printed out by quillprint.com as a squared corners business card (see artwork and design guidelines here: https://help.quillprint.com/hc/en-gb/sections/200570950-QUILL-Product-Templates)

The design should be clean and modern and reflect the colours, tone and branding on my website: https://tessavorrin.com.au

Target Market(s)

Professionals, B2B small business owners

Industry/Entity Type

Business

Contact Information for Business Card

Tessa Vorrin
m: 0468 905 327
e: tessa@tessavorrin.com.au
w: tessavorrin.com.au

Font styles to use
Sans Serif

Requirements
Must have
• Tagline: "Smart copywriting for clever business people"
• Brand colours: fd8000, 009984, 666666 and black
Nice to have

```html
<!DOCTYPE html>
<html lang="en">
<head>
<meta charset="utf-8">
<title>Tessa Vorrin – Business Card</title>
<link rel="stylesheet" href="https://fonts.googleapis.com/css2?family=Lato:wght@400;700&family=Tinos:ital,wght@1,700&display=swap">
<style>
  :root {
    --brand-orange: #fd8000;
    --brand-teal: #009984;
    --brand-teal-light: #35a790;
    --brand-teal-dark: #2a8f7a;
    --brand-grey: #666666;
    --ink: #111111;
    --paper: #ffffff;
    --backdrop: #eeeeee;
  }
  * { box-sizing: border-box; margin: 0; padding: 0; }
  html, body {
    width: 1200px;
    height: 586px;
    overflow: hidden;
    background: var(--backdrop);
    font-family: "Lato", sans-serif;
  }
  .canvas {
    position: relative;
    width: 1200px;
    height: 586px;
  }
  .card {
    position: absolute;
    top: 129px;
    width: 501px;
    height: 301px;
    overflow: hidden;
  }
  .card--front { left: 61px; }
  .card--back { left: 619px; background: var(--paper); }

  /* Front */
  .front-texture {
    position: absolute;
    inset: 0;
    background: linear-gradient(135deg, var(--brand-teal-light) 0%, var(--brand-teal-dark) 55%, var(--brand-teal-light) 100%);
  }
  .front-name {
    position: absolute;
    left: 0; right: 0;
    top: 112px;
    text-align: center;
    color: var(--paper);
    font-size: 48px;
    font-weight: 400;
    letter-spacing: -0.5px;
  }
  .front-tagline {
    position: absolute;
    left: 0; right: 0;
    top: 248px;
    text-align: center;
    color: #1f3a33;
    font-family: "Tinos", serif;
    font-style: italic;
    font-weight: 700;
    font-size: 12px;
  }

  /* Back */
  .back-name {
    position: absolute;
    left: 30px;
    top: 45px;
    color: var(--brand-teal);
    font-size: 35px;
    font-weight: 400;
    letter-spacing: -0.5px;
  }
  .contact-list {
    position: absolute;
    left: 26px;
    top: 211px;
    list-style: none;
  }
  .contact-item {
    display: flex;
    align-items: center;
    height: 24px;
    font-size: 12px;
    color: var(--ink);
  }
  .contact-icon {
    width: 17px;
    height: 17px;
    margin-right: 7px;
  }
  .contact-web {
    color: var(--brand-teal);
    font-weight: 700;
    font-size: 12px;
    height: 20px;
    display: flex;
    align-items: center;
  }
  .social-row {
    position: absolute;
    right: 27px;
    top: 190px;
    display: flex;
    gap: 3px;
  }
  .social-dot {
    width: 23px;
    height: 23px;
    border-radius: 50%;
    background: var(--brand-orange);
  }
  .services {
    position: absolute;
    right: 28px;
    top: 222px;
    text-align: right;
    font-size: 11px;
    line-height: 18.5px;
    color: var(--ink);
    list-style: none;
  }
</style>
</head>
<body>
<main class="canvas">

  <section class="card card--front" aria-label="Card front">
    <div class="front-texture" role="img" aria-label="Teal low-poly faceted background pattern"></div>
    <h1 class="front-name">Tessa Vorrin</h1>
    <p class="front-tagline">Smart copywriting for clever business people</p>
  </section>

  <section class="card card--back" aria-label="Card back">
    <h2 class="back-name">Tessa Vorrin</h2>

    <ul class="contact-list">
      <li class="contact-item">
        <svg class="contact-icon" viewBox="0 0 20 20" aria-hidden="true">
          <circle cx="10" cy="10" r="10" fill="var(--brand-teal)"/>
          <path d="M5 8.5c0-1.5 2-2.5 5-2.5s5 1 5 2.5l-1.5 0.6-1-1.2h-5l-1 1.2z M6.5 9.5h7l0.8 4.5h-8.6z" fill="#fff"/>
        </svg>
        0468 905 327
      </li>
      <li class="contact-item">
        <svg class="contact-icon" viewBox="0 0 20 20" aria-hidden="true">
          <circle cx="10" cy="10" r="10" fill="var(--brand-teal)"/>
          <rect x="5" y="6.5" width="10" height="7" fill="#fff"/>
          <path d="M5 6.5l5 4 5-4" fill="none" stroke="var(--brand-teal)" stroke-width="1"/>
        </svg>
        tessa@tessavorrin.com.au
      </li>
      <li class="contact-web">www.tessavorrin.com.au</li>
    </ul>

    <div class="social-row" aria-label="Social profiles">
      <span class="social-dot"></span>
      <span class="social-dot"></span>
      <span class="social-dot"></span>
      <span class="social-dot"></span>
    </div>

    <ul class="services">
      <li>SEO Copywriting, Feature Writing</li>
      <li>Content Marketing, Legal Copywriting</li>
      <li>Small Business Copywriting, Website Copywriting</li>
    </ul>
  </section>

</main>
</body>
</html>
```